V.Lumo Gin - Bottle label Design

We are manufacturers of Gin in South Africa.
The name of our Gin is V.Lumo Gin with Q standing for Dlovikazi, a Xhosa Village in the region of Eastern Cape.

We would like our brand to depict the following (really the focus of Gold on it)
> Prosperity of the place
> Wealth of the place, land, material or in the people
> Gold rush, potential, hope

As the brand matures, we would like to have campaigns with it. See ideas below:
> V.Lumo Premium
> Crimson dusk edition
Limited edition will be released every year
- V.Lumo entabeni (location)
- V.Lumo ekhayeni (location)

> Each batch of bottles with focus on a specific area/location in Dlovikazi. One that is known and will be highlighted on the map design of the bottle.
Bottles based on landmarks in Dlovikazi and landmark design in the Big V.

Below we tried but we are not where we really want to be in terms of Gin Bottle elegance.

Target Market(s)

Target market is the young crowd. Young Xhosa men and women working really hard to get their goals. Positive thinkers. Elegant. Fresh. Bold. Age from 24 to 45. People who enjoy quality products.

Industry/Entity Type

Beverage Industry. Craft Gin.

Font styles to use
Sans Serif
Decorative

Colors
FFF300
FFF600
FEFA6F
FFFEC7
FFFEE8
FFC000
F8CF3A
FAE287
FDF2CF
FEFAEE

Requirements
Must have
• Gold colour as a theme. Try and make the background textured.

```html
<!DOCTYPE html>
<html lang="en">
<head>
<meta charset="utf-8">
<title>V.Lumo Gin – Bottle Label</title>
<link rel="stylesheet" href="https://fonts.googleapis.com/css2?family=Josefin+Sans:wght@100;300&family=Oswald:wght@400;500&display=swap">
<style>
  :root {
    --backdrop: #e0dbcf;
    --label: #ffffff;
    --ink: #111111;
    --ink-soft: #2a2a2a;
    --gold-deep: #7a4f10;
    --gold-mid: #b8862a;
    --gold-bright: #e3e36a;
    --gold-pale: #fae287;
    --earth: #c8742e;
    --grass: #e8d98a;
    --sky: #fffee8;
    --map-wash: #f5f5f6;
    --rule: #222222;
  }
  * { box-sizing: border-box; margin: 0; padding: 0; }
  html, body { width: 1200px; height: 1200px; overflow: hidden; }
  body { background: var(--backdrop); position: relative; font-family: "Oswald", sans-serif; }

  .label {
    position: absolute; left: 96px; top: 197px;
    width: 1008px; height: 805px;
    background: var(--label);
  }
  .pattern-band {
    position: absolute; left: 46px; width: 917px; height: 38px;
    background: linear-gradient(90deg, var(--gold-deep), var(--gold-mid) 20%, var(--gold-bright) 40%, var(--gold-mid) 60%, var(--gold-deep) 80%, var(--gold-mid));
    opacity: .85;
  }
  .pattern-band.top { top: 20px; }
  .pattern-band.bottom { top: 747px; }

  .landscape {
    position: absolute; left: 47px; top: 79px; width: 915px; height: 354px;
    background: linear-gradient(180deg, var(--sky) 0%, var(--gold-pale) 18%, var(--gold-mid) 30%, var(--grass) 50%, var(--earth) 68%, var(--grass) 82%, #f7f1d6 100%);
  }

  .village-map {
    position: absolute; left: 47px; top: 499px; width: 236px; height: 233px;
    background: linear-gradient(160deg, var(--map-wash), #ececef);
  }

  .brand-mark {
    position: absolute; left: 180px; top: 322px;
    display: flex; align-items: center; gap: 22px;
  }
  .brand-mark .dot {
    width: 200px; height: 200px; border-radius: 50%;
    background: linear-gradient(90deg, var(--gold-mid), var(--gold-bright) 35%, var(--gold-mid) 65%, var(--gold-deep));
    border: 6px solid var(--label);
  }
  .brand-mark .name {
    font-family: "Josefin Sans", sans-serif; font-weight: 300;
    font-size: 118px; line-height: 1; color: var(--ink);
    letter-spacing: 2px; margin-top: 90px;
  }

  .spec-table {
    position: absolute; left: 47px; top: 587px; width: 915px; height: 146px;
    border: 2px dotted var(--rule);
    display: grid;
    grid-template-columns: 306px 298px 1fr;
    grid-template-rows: 74px 1fr;
  }
  .spec-table > div { display: flex; align-items: center; justify-content: center; }
  .cell-kind {
    grid-row: 1 / 3; grid-column: 1;
    border-right: 2px dotted var(--rule);
    font-family: "Josefin Sans", sans-serif; font-weight: 100;
    font-size: 122px; color: var(--ink); letter-spacing: 6px;
    padding-top: 22px; justify-content: flex-start !important; padding-left: 30px;
  }
  .cell-tagline {
    grid-column: 2 / 4; grid-row: 1;
    border-bottom: 2px dotted var(--rule);
    font-size: 27px; color: var(--ink-soft); letter-spacing: 2.4px; font-weight: 400;
  }
  .cell-abv, .cell-volume { font-size: 28px; color: var(--ink); font-weight: 500; }
  .cell-abv { grid-column: 2; grid-row: 2; border-right: 2px dotted var(--rule); }
  .cell-volume { grid-column: 3; grid-row: 2; }
</style>
</head>
<body>
  <main class="label">
    <div class="pattern-band top" role="img" aria-label="Gold geometric diamond and chevron border pattern"></div>

    <div class="landscape" role="img" aria-label="Golden-toned illustration of Dlovikazi village: hill, houses, fences and grassland"></div>

    <div class="village-map" role="img" aria-label="Faint street map of Dlovikazi"></div>

    <div class="brand-mark">
      <span class="dot"></span>
      <span class="name">V.Lumo</span>
    </div>

    <section class="spec-table">
      <div class="cell-kind">GIN</div>
      <div class="cell-tagline">Our Golden Gift from Dlovikazi to the World</div>
      <div class="cell-abv">43% alc.vol.</div>
      <div class="cell-volume">750 ml</div>
    </section>

    <div class="pattern-band bottom" role="img" aria-label="Gold geometric diamond and chevron border pattern"></div>
  </main>
</body>
</html>
```